Fresh, modern, fun business card for pediatric dental practice

Need a business card for fresh, modern, fun pediatric dental practice

Clean look that matches our website's font and colors

We prefer the look of curved corners on business cards

Target Market(s)

parents (mothers) of young children, professionals, mid-high class

Industry/Entity Type

Dental

Contact Information for Business Card

Maplebrook Pediatric Dentistry
482 Quarry Lane
Suite 517
Fernwick, PA 17890
717.555.0193
www.maplebrookkidsdental.example

Mei-Ran Tsai, DMD
Corinne Walbeck, DMD
(we are working on our email address, but we would like that on the card as well)

Font styles to use
Sans Serif

Requirements
Must have
• All info; we would also like to make cards for individual staff members
• colors from our website and color palatte, attatched
• use same font and design as website for branding
Nice to have
• clean, simple card that has a pop of color
• we would like to see a few designs with our tag line "where smiles get brighter"
• we are not sure if we want to have it on there or not
• we would like to see a few designs incorporating the ribbon graphic on our website where the word WELCOME is

```html
<!DOCTYPE html>
<html lang="en">
<head>
<meta charset="utf-8">
<title>Maplebrook Pediatric Dentistry – Business Cards</title>
<link href="https://fonts.googleapis.com/css2?family=Roboto+Condensed:wght@500&family=Ubuntu:wght@400;700&family=Lato:wght@400;700&display=swap" rel="stylesheet">
<style>
  :root {
    --magenta: #d12a8e;
    --sun: #f7b41c;
    --paper: #ffffff;
    --ink: #4a4a4a;
    --backdrop: #474543;
  }
  * { box-sizing: border-box; margin: 0; padding: 0; }
  html, body { width: 1200px; height: 960px; overflow: hidden; }
  body { background: var(--backdrop); position: relative; font-family: "Lato", sans-serif; }

  .card {
    position: absolute;
    width: 476px;
    height: 268px;
    border-radius: 14px;
    overflow: hidden;
    box-shadow: 0 3px 6px rgba(0,0,0,.35);
  }
  .card--front { background: linear-gradient(160deg, #ffffff 40%, #f1f1f1); left: 110px; }
  .card--back { background: var(--magenta); left: 611px; }
  .row-top { top: 184px; }
  .row-bottom { top: 502px; }

  .name-ribbon {
    position: absolute;
    left: 0; top: 62px;
    height: 38px;
    padding: 0 38px 0 20px;
    background: var(--magenta);
    clip-path: polygon(0 0, 100% 0, calc(100% - 14px) 50%, 100% 100%, 0 100%);
    display: flex; align-items: center;
    font-family: "Roboto Condensed", sans-serif;
    font-weight: 500;
    font-size: 21px;
    color: #fff;
    white-space: nowrap;
  }
  .name-ribbon .credential { color: var(--sun); margin-left: 5px; }

  .brand {
    position: absolute;
    display: flex; flex-direction: column; align-items: center;
    font-family: "Ubuntu", sans-serif;
    line-height: 1;
  }
  .brand__mark { border-radius: 50%; }
  .brand__name { font-weight: 700; letter-spacing: .04em; }
  .brand__tag { font-weight: 400; letter-spacing: .09em; margin-top: 3px; }

  .brand--front { right: 22px; top: 22px; color: var(--sun); }
  .brand--front .brand__mark { width: 30px; height: 30px; border: 3px solid var(--sun); margin-bottom: 10px; }
  .brand--front .brand__name { font-size: 25px; }
  .brand--front .brand__tag { font-size: 14px; color: var(--magenta); }

  .brand--back { left: 50%; top: 50%; transform: translate(-50%, -50%); color: #fff; }
  .brand--back .brand__mark { width: 38px; height: 38px; border: 3px solid #fff; margin-bottom: 10px; }
  .brand--back .brand__name { font-size: 36px; }
  .brand--back .brand__tag { font-size: 19px; }

  .brand--pattern { left: 50%; top: 50%; transform: translate(-50%, -50%); color: #fff; background: var(--magenta); padding: 8px 10px; }
  .brand--pattern .brand__name { font-size: 31px; }
  .brand--pattern .brand__tag { font-size: 16px; }

  .contact { position: absolute; left: 20px; top: 134px; font-size: 11.5px; color: var(--ink); line-height: 15px; }
  .contact__practice { color: var(--magenta); font-weight: 700; }
  .contact__list { list-style: none; margin-top: 14px; }
  .contact__list li { display: flex; align-items: center; gap: 5px; height: 17px; }
  .contact__icon { width: 13px; height: 13px; flex: none; }

  .pattern-field { position: absolute; inset: 0; background: var(--magenta); }
</style>
</head>
<body>

<svg width="0" height="0" style="position:absolute" aria-hidden="true">
  <symbol id="icon-phone" viewBox="0 0 16 16">
    <circle cx="8" cy="8" r="8" fill="#d12a8e"/>
    <path d="M5.2 4.2l1.4-.2.8 2-1 .8c.5 1.1 1.3 1.9 2.4 2.4l.8-1 2 .8-.2 1.4c-3.4.2-6.4-2.8-6.2-6.2z" fill="#fff"/>
  </symbol>
  <symbol id="icon-mail" viewBox="0 0 16 16">
    <circle cx="8" cy="8" r="8" fill="#d12a8e"/>
    <rect x="4" y="5" width="8" height="6" rx="1" fill="#fff"/>
    <path d="M4.3 5.4L8 8.3l3.7-2.9" stroke="#d12a8e" stroke-width="1" fill="none"/>
  </symbol>
  <symbol id="icon-web" viewBox="0 0 16 16">
    <circle cx="8" cy="8" r="8" fill="#d12a8e"/>
    <circle cx="8" cy="8" r="4" fill="none" stroke="#fff" stroke-width="1.2"/>
    <path d="M4 8h8M8 4c-1.6 2.4-1.6 5.6 0 8M8 4c1.6 2.4 1.6 5.6 0 8" stroke="#fff" stroke-width="1" fill="none"/>
  </symbol>
</svg>

<section class="card card--front row-top">
  <div class="name-ribbon">Mei-Ran Tsai,<span class="credential">DMD</span></div>
  <div class="brand brand--front">
    <span class="brand__mark"></span>
    <span class="brand__name">maplebrook</span>
    <span class="brand__tag">pediatric dentistry</span>
  </div>
  <div class="contact">
    <p class="contact__practice">Maplebrook Pediatric Dentistry</p>
    <p>482 Quarry Lane, Suite 517</p>
    <p>Fernwick, PA 17890</p>
    <ul class="contact__list">
      <li><svg class="contact__icon"><use href="#icon-phone"/></svg>717.555.0193</li>
      <li><svg class="contact__icon"><use href="#icon-mail"/></svg>info@maplebrookkidsdental.example</li>
      <li><svg class="contact__icon"><use href="#icon-web"/></svg>www.maplebrookkidsdental.example</li>
    </ul>
  </div>
</section>

<section class="card card--back row-top">
  <div class="brand brand--back">
    <span class="brand__mark"></span>
    <span class="brand__name">maplebrook</span>
    <span class="brand__tag">pediatric dentistry</span>
  </div>
</section>

<section class="card card--front row-bottom">
  <div class="name-ribbon">Corinne Walbeck,<span class="credential">DMD</span></div>
  <div class="brand brand--front">
    <span class="brand__mark"></span>
    <span class="brand__name">maplebrook</span>
    <span class="brand__tag">pediatric dentistry</span>
  </div>
  <div class="contact">
    <p class="contact__practice">Maplebrook Pediatric Dentistry</p>
    <p>482 Quarry Lane, Suite 517</p>
    <p>Fernwick, PA 17890</p>
    <ul class="contact__list">
      <li><svg class="contact__icon"><use href="#icon-phone"/></svg>717.555.0193</li>
      <li><svg class="contact__icon"><use href="#icon-mail"/></svg>info@maplebrookkidsdental.example</li>
      <li><svg class="contact__icon"><use href="#icon-web"/></svg>www.maplebrookkidsdental.example</li>
    </ul>
  </div>
</section>

<section class="card card--back row-bottom">
  <div class="pattern-field" role="img" aria-label="Repeating pattern of small orange spiral sun motifs on magenta"></div>
  <div class="brand brand--pattern">
    <span class="brand__name">maplebrook</span>
    <span class="brand__tag">pediatric dentistry</span>
  </div>
</section>

</body>
</html>
```